13 Varno - new website design project

Our company Varno Electrical is developing a new lead generation website focused on Electrical, LED Lighting and Solar Power. We need a high converting website.

Example of our current website is www.varnoelectrical-example.com.au You can take content from this website for this new design. Our colours are red, black and white. For our new website we would like to promote Varno, Spark Every Day. Please listen to the jingle.

The below link is the company jingle that we have developed.
http://www.tunecraftdemo.com.au/vrn-tc-v1/

The key for this brief is to generate leads for Electrical, LED Lighting (for commercial) and Solar Power & Storage.

Target Market(s)

Business owners in Melbourne Victoria

Number of Pages Required

4 page

Colors
ec1f27
ffffff

Requirements
Must have
• This page must be clean, be in line with company branding and a high converting lead website.

```html
<!DOCTYPE html>
<html lang="en">
<head>
<meta charset="utf-8">
<title>Contact Us – Varno Electrical</title>
<link rel="stylesheet" href="https://fonts.googleapis.com/css2?family=Lato:wght@400;700;900&family=Open+Sans:wght@400;600&display=swap">
<style>
:root{
  --red:#ec1f27;
  --dark:#30333b;
  --text:#333;
  --muted:#555;
  --line:#bbb;
  --white:#fff;
}
*{box-sizing:border-box;margin:0;padding:0}
html,body{width:1200px;height:1069px;overflow:hidden;background:var(--white)}
body{position:relative;font-family:"Open Sans",sans-serif;color:var(--text)}
.abs{position:absolute}
.topline{left:0;top:0;width:1200px;height:3px;background:var(--dark)}
.topline::before{content:"";position:absolute;left:0;top:0;width:624px;height:3px;background:var(--red)}
.brand{left:99px;top:32px;display:flex;align-items:center;gap:8px;font-family:"Lato",sans-serif;font-weight:900;font-size:30px;color:var(--dark);letter-spacing:1px}
.brand-mark{width:14px;height:14px;background:var(--red);border-radius:50%}
.top-contact{top:15px;display:flex;align-items:center;gap:12px;font-family:"Lato",sans-serif;font-size:15.5px;color:var(--text);white-space:nowrap}
.ring{width:33px;height:33px;border:1px solid #aaa;border-radius:50%;display:flex;align-items:center;justify-content:center}
.nav{top:64px;left:357px;display:flex;font-family:"Lato",sans-serif;font-weight:700;font-size:15px;color:var(--dark)}
.nav span{position:absolute;white-space:nowrap}
.nav .active{color:var(--red)}
.hero{left:0;top:94px;width:1200px;height:303px;background:linear-gradient(180deg,#b39a55 0%,#e6d79a 40%,#8d8760 70%,#5c6b2d 100%)}
.hero .hero-title{position:absolute;left:0;right:0;top:112px;text-align:center;font-family:"Lato",sans-serif;font-weight:700;font-size:64px;line-height:76px;color:var(--white);text-shadow:0 2px 6px rgba(0,0,0,.35);text-decoration:none}
.dots{top:354px;left:530px;display:flex;gap:6px}
.dots i{width:31px;height:4px;background:var(--white);display:block}
.dots i:first-child{background:var(--red)}
.crumb{left:98px;top:428px;font-family:"Lato",sans-serif;font-size:16px;font-weight:700;color:var(--dark)}
.crumb b{color:var(--red);font-weight:700}
.crumb em{font-style:normal;margin:0 8px;font-size:13px}
.rule{left:99px;top:471px;width:1002px;height:1px;background:var(--line)}
.h2{font-family:"Lato",sans-serif;font-weight:700;font-size:27px;color:var(--dark)}
.sub{left:99px;top:598px;font-size:19px;color:var(--dark)}
.label{font-size:13px;color:var(--muted)}
.field{border:1px solid var(--line);background:var(--white)}
.select-arrow{position:absolute;right:0;top:0;width:39px;height:100%;border-left:1px solid var(--line)}
.select-arrow::after{content:"";position:absolute;left:15px;top:14px;border:5px solid transparent;border-top-color:#888}
.submit{left:588px;top:896px;width:116px;height:40px;background:var(--red);overflow:hidden;color:var(--white);font-family:"Lato",sans-serif;font-weight:700;font-size:16px;letter-spacing:.5px}
.submit span{position:absolute;left:17px;top:11px}
.submit svg{position:absolute;right:0;top:0}
.address{left:751px;top:538px;width:350px;height:398px;border:1px solid var(--line)}
.addr-row{left:780px;width:310px;display:flex;align-items:flex-start;gap:20px;font-size:14.5px;color:var(--muted);line-height:24px}
.addr-row .ring{width:43px;height:43px;flex:none}
.addr-mail{font-size:12.5px;letter-spacing:-.1px;white-space:nowrap}
.footer{left:0;top:1005px;width:1200px;height:64px}
.copy{left:99px;top:1029px;font-size:12.5px;color:var(--white)}
.social{left:976px;top:1029px;display:flex;gap:6px}
.social i{width:27px;height:27px;border:1.5px solid var(--white);border-radius:50%;display:block}
</style>
</head>
<body spellcheck="false">
<div class="abs topline"></div>

<header>
  <div class="abs brand"><span class="brand-mark"></span>Varno</div>
  <div class="abs top-contact" style="left:671px">
    <span class="ring"><svg width="14" height="14" viewBox="0 0 24 24"><path fill="#ec1f27" d="M6.6 10.8a15.1 15.1 0 0 0 6.6 6.6l2.2-2.2c.3-.3.7-.4 1-.2 1.1.4 2.3.6 3.6.6.6 0 1 .4 1 1V20c0 .6-.4 1-1 1C10.6 21 3 13.4 3 4c0-.6.4-1 1-1h3.5c.6 0 1 .4 1 1 0 1.3.2 2.5.6 3.6.1.3 0 .7-.2 1z"/></svg></span>
    <span>1300 555 827</span>
  </div>
  <div class="abs top-contact" style="left:844px">
    <span class="ring"><svg width="14" height="11" viewBox="0 0 24 18"><path fill="#ec1f27" d="M0 2 12 10 24 2V0H0zM0 5v13h24V5l-12 8z"/></svg></span>
    <span style="font-size:13.5px">service@varnoelectrical-example.com.au</span>
  </div>
  <nav class="abs nav">
    <span style="left:0">HOME</span>
    <span style="left:87px">VARNO STORY</span>
    <span style="left:221px">SERVICES</span>
    <span style="left:329px">OUR WORK</span>
    <span style="left:453px">SOLAR POWER</span>
    <span class="active" style="left:600px">CONTACT US</span>
    <svg style="position:absolute;left:740px;top:3px" width="14" height="14" viewBox="0 0 14 14"><circle cx="6" cy="6" r="4.5" fill="none" stroke="#30333b" stroke-width="2"/><path d="M9.2 9.2 13 13" stroke="#30333b" stroke-width="2.4"/></svg>
  </nav>
</header>

<section class="abs hero" role="img" aria-label="Rows of solar panels under a sunset sky with a pylon and wind turbine">
  <h1 class="hero-title">Contact us</h1>
</section>
<div class="abs dots"><i></i><i></i><i></i><i></i></div>

<div class="abs crumb">HOME<em>&gt;&gt;</em><b>CONTACT US</b></div>
<div class="abs rule"></div>

<main>
  <h2 class="abs h2" style="left:99px;top:528px">CONTACT US</h2>
  <p class="abs sub">Get In Touch:</p>

  <label class="abs label" style="left:99px;top:656px">Name :</label>
  <div class="abs field" style="left:99px;top:677px;width:297px;height:33px"></div>
  <label class="abs label" style="left:406px;top:655px">Email :</label>
  <div class="abs field" style="left:407px;top:677px;width:297px;height:33px"></div>

  <label class="abs label" style="left:99px;top:725px">Phone :</label>
  <div class="abs field" style="left:99px;top:747px;width:297px;height:33px"></div>
  <label class="abs label" style="left:406px;top:724px">Purpose :</label>
  <div class="abs field" style="left:407px;top:747px;width:297px;height:33px"><span class="select-arrow"></span></div>

  <label class="abs label" style="left:99px;top:793px">Message :</label>
  <div class="abs field" style="left:99px;top:816px;width:605px;height:59px"></div>

  <div class="abs submit"><span>SUBMIT</span>
    <svg width="40" height="40" viewBox="0 0 40 40"><path d="M0 0H40V40Z" fill="#30333b"/></svg>
  </div>

  <aside class="abs address">
    <h2 class="h2" style="position:absolute;left:28px;top:19px">ADDRESS</h2>
  </aside>
  <div class="abs addr-row" style="top:630px">
    <span class="ring"><svg width="12" height="17" viewBox="0 0 12 17"><path fill="#ec1f27" d="M6 0a6 6 0 0 0-6 6c0 4.5 6 11 6 11s6-6.5 6-11a6 6 0 0 0-6-6zm0 8.5A2.5 2.5 0 1 1 6 3.5a2.5 2.5 0 0 1 0 5z"/></svg></span>
    <span>24/88 Harlow St<br>Glen Ridge<br>VIC 3150</span>
  </div>
  <div class="abs addr-row" style="top:734px">
    <span class="ring"><svg width="17" height="17" viewBox="0 0 24 24"><path fill="#ec1f27" d="M6.6 10.8a15.1 15.1 0 0 0 6.6 6.6l2.2-2.2c.3-.3.7-.4 1-.2 1.1.4 2.3.6 3.6.6.6 0 1 .4 1 1V20c0 .6-.4 1-1 1C10.6 21 3 13.4 3 4c0-.6.4-1 1-1h3.5c.6 0 1 .4 1 1 0 1.3.2 2.5.6 3.6.1.3 0 .7-.2 1z"/></svg></span>
    <span style="padding-top:9px">1300 555 827</span>
  </div>
  <div class="abs addr-row" style="top:820px">
    <span class="ring"><svg width="19" height="14" viewBox="0 0 24 18"><path fill="#ec1f27" d="M0 2 12 10 24 2V0H0zM0 5v13h24V5l-12 8z"/></svg></span>
    <span class="addr-mail" style="padding-top:9px">service@varnoelectrical-example.com.au</span>
  </div>
</main>

<footer>
  <svg class="abs footer" width="1200" height="64" viewBox="0 0 1200 64">
    <rect x="0" y="12" width="1200" height="52" fill="#30333b"/>
    <path d="M0 0H634L654 12L684 64H0Z" fill="#ec1f27"/>
    <path d="M634 0H620L652 64H666Z" fill="#fff"/>
  </svg>
  <p class="abs copy">Copyrights © 2017, Varno Electrical. All rights reserved.</p>
  <div class="abs social"><i></i><i></i><i></i><i></i></div>
</footer>
</body>
</html>
```